indépendant en tant que Massothérapeute et Préparateur Mental, j'ai besoin de ...

Massothérapeute et préparateur mental indépendant, je recherche une carte de visite sobre et dynamique, sans images liées au massage ou à la préparation mentale mais intégrant mon logo. Les couleurs que j'aime bien sont : Blanc, gris, anthracite, noir et jaune

Contact Information for Business Card

carte de préférence Horizontale
neutre qui puisse toucher le deux domaines Massothérapie et préparation mentale

Requirements
Must have
• mon projet doit intégrer au recto:
LOGO
Loïc Bardèze
078 513 26 48
info@loicbardeze.ch
et éventuellement www.loicbardeze.ch

et au verso les deux adresses:

Chemin des Ormilles 7B
1450 Valmont-sur-Lac

Route de la Gravière 9
1720 Montbrizon

Should not have
• mon projet ne doit pas contenir d'image en liens avec le massage ni la préparation mentale.

```html
<!DOCTYPE html>
<html lang="fr">
<head>
<meta charset="utf-8">
<title>Loïc Bardèze – Carte de visite</title>
<link rel="stylesheet" href="https://fonts.googleapis.com/css2?family=Work+Sans:wght@400;500;600&display=swap">
<style>
  :root {
    --page: #2b2b2b;
    --card: #2a2a2b;
    --card-deep: #1f1f20;
    --white: #ffffff;
    --soft: #d9d9d9;
    --yellow: #f5b800;
    --photo-warm: #6b5a52;
    --photo-dark: #3a3736;
  }
  * { box-sizing: border-box; margin: 0; padding: 0; }
  html, body { width: 1200px; height: 930px; overflow: hidden; }
  body {
    background: var(--page);
    font-family: "Work Sans", sans-serif;
    color: var(--white);
    position: relative;
  }
  .card {
    position: absolute;
    top: 290px;
    width: 540px;
    height: 350px;
    border-radius: 18px;
    background: linear-gradient(135deg, var(--card) 0%, var(--card-deep) 100%);
    overflow: hidden;
    box-shadow: 0 14px 30px rgba(0,0,0,.45);
  }
  .card--front { left: 40px; }
  .card--back { left: 620px; }

  .front-visual {
    position: absolute;
    left: 130px; top: 40px;
    width: 300px; height: 290px;
    border-radius: 50% 50% 40% 40%;
    background: radial-gradient(ellipse at 50% 45%, var(--photo-warm) 0%, var(--photo-dark) 55%, transparent 75%);
    opacity: .85;
  }
  .brand {
    position: absolute;
    display: flex;
    align-items: center;
    gap: 10px;
  }
  .brand__name {
    font-weight: 600;
    color: var(--white);
    letter-spacing: .02em;
    line-height: 1;
  }
  .brand__dot {
    width: 12px; height: 12px;
    border-radius: 50%;
    background: var(--white);
  }
  .brand__role {
    position: absolute;
    font-size: 11px;
    letter-spacing: .06em;
    color: var(--soft);
    text-transform: uppercase;
    white-space: nowrap;
  }
  .card--front .brand { left: 120px; top: 150px; }
  .card--front .brand__name { font-size: 34px; }
  .card--front .brand__role { left: 144px; top: 196px; }

  .card--back .brand { left: 34px; top: 40px; }
  .card--back .brand__name { font-size: 22px; }
  .card--back .brand__role { left: 56px; top: 70px; font-size: 9px; }

  .side-mark {
    position: absolute;
    right: 30px; top: 30px;
    height: 290px;
    writing-mode: vertical-rl;
    font-size: 44px;
    font-weight: 600;
    line-height: 1;
    color: var(--white);
    text-align: center;
    white-space: nowrap;
  }

  .identity {
    position: absolute;
    left: 34px; top: 112px;
    padding-left: 14px;
    border-left: 5px solid var(--yellow);
  }
  .identity__name {
    font-size: 24px;
    font-weight: 500;
    color: var(--yellow);
    letter-spacing: .04em;
    text-transform: uppercase;
    line-height: 1.2;
  }
  .identity__title { font-size: 15px; margin-top: 2px; }

  .contacts {
    position: absolute;
    left: 52px; top: 176px;
    list-style: none;
    font-size: 15px;
    line-height: 1.45;
  }
  .contacts li { display: flex; align-items: center; gap: 8px; }
  .contacts svg { width: 12px; height: 12px; flex: none; }

  .addresses {
    position: absolute;
    left: 72px; top: 248px;
    font-size: 14px;
    line-height: 1.35;
    font-style: normal;
  }
  .addresses p + p { margin-top: 6px; }
</style>
</head>
<body>

<section class="card card--front" aria-label="Recto">
  <div class="front-visual" role="img" aria-label="Photo d'un enfant torse nu, mains sur les hanches, devant un dessin de bras musclés"></div>
  <div class="brand">
    <span class="brand__dot"></span>
    <span class="brand__name">Loïc Bardèze</span>
  </div>
  <span class="brand__role">Massothérapeute / Préparateur mental</span>
</section>

<section class="card card--back" aria-label="Verso">
  <div class="brand">
    <span class="brand__dot"></span>
    <span class="brand__name">Loïc Bardèze</span>
  </div>
  <span class="brand__role">Massothérapeute / Préparateur mental</span>

  <div class="side-mark">Loïc Bardèze</div>

  <div class="identity">
    <p class="identity__name">Loïc Bardèze</p>
    <p class="identity__title">Director</p>
  </div>

  <ul class="contacts">
    <li>
      <svg viewBox="0 0 12 12" aria-hidden="true"><path d="M3 1 L5 3.5 L4 5 Q5.5 7 7 8 L8.5 7 L11 9 L9.5 11 Q4 10 1 2.5 Z" fill="var(--yellow)"/></svg>
      078 513 26 48
    </li>
    <li>
      <svg viewBox="0 0 12 12" aria-hidden="true"><rect x="1" y="2.5" width="10" height="7" fill="none" stroke="var(--yellow)" stroke-width="1.3"/><path d="M1 2.5 L6 6.5 L11 2.5" fill="none" stroke="var(--yellow)" stroke-width="1.3"/></svg>
      info@loicbardeze.ch
    </li>
    <li>
      <svg viewBox="0 0 12 12" aria-hidden="true"><circle cx="6" cy="6" r="5" fill="none" stroke="var(--yellow)" stroke-width="1.2"/><ellipse cx="6" cy="6" rx="2.2" ry="5" fill="none" stroke="var(--yellow)" stroke-width="1"/><path d="M1 6 H11" stroke="var(--yellow)" stroke-width="1"/></svg>
      www.loicbardeze.ch
    </li>
  </ul>

  <address class="addresses">
    <p>Chemin des Ormilles 7B<br>1450 Valmont-sur-Lac</p>
    <p>Route de la Gravière 9<br>1720 Montbrizon</p>
  </address>
</section>

</body>
</html>
```